Automotive component supplier needs a business card design

We need a business card design for our company called Velran Global Components Ltd based in the UK. We are a supplier of interior and exterior components to premium car manufacturers such as Corvel Ashby, Hadley Fenn, Marquist and Tavarelli. We would like to see a modern business card design that uses the colour blue.

Target Market(s)

Premium automotive car manufacturers.

Industry/Entity Type

Automotive

Contact Information for Business Card

Company Name : Velran Global Components Limited
Address: 17 Marlow Yard, Upper Heath, Warwick, CV31 8QL, United Kingdom
Web Address : www.velrancomponents-example.co.uk

Font styles to use
Other font styles liked:
• Helvetica

Colors
3176b5
0255a3
85acd3
cfdeed
cee9f5
85cae6
34a6d7
0692cd
9bcb3c

Requirements
Must have
• Clear company logo and a mixture of blue colours.
Nice to have
• A high quality modern image.
Should not have
• Multiple colours.

```html
<!DOCTYPE html>
<html lang="en">
<head>
<meta charset="utf-8">
<title>Velran Global Components – Business Card</title>
<link href="https://fonts.googleapis.com/css2?family=Arimo:wght@400;700&display=swap" rel="stylesheet">
<style>
  :root {
    --blue-bright: #0692cd;
    --blue-mid: #34a6d7;
    --blue-deep: #0255a3;
    --green: #9bcb3c;
    --white: #ffffff;
    --stage: #2b2c2e;
  }
  * { box-sizing: border-box; margin: 0; padding: 0; }
  html, body {
    width: 1200px; height: 900px; overflow: hidden;
    background: var(--stage);
    font-family: "Arimo", "Helvetica Neue", Helvetica, Arial, sans-serif;
  }
  .canvas { position: relative; width: 1200px; height: 900px; }
  .card {
    position: absolute; width: 700px; height: 400px; overflow: hidden;
    box-shadow: 0 10px 30px rgba(0,0,0,.45);
  }
  .card--back { left: 80px; top: 30px; }
  .card--front { left: 420px; top: 470px; background: var(--white); }

  .back-field {
    position: absolute; inset: 0;
    background: linear-gradient(135deg, var(--blue-mid), var(--blue-bright));
  }
  .back-name {
    position: absolute; right: 40px; bottom: 130px;
    color: var(--white); font-weight: 700; font-size: 22px; letter-spacing: .5px;
  }

  .front-shapes { position: absolute; inset: 0; }
  .brand-name {
    position: absolute; left: 40px; top: 118px; width: 330px;
    color: var(--blue-bright); font-weight: 700; font-size: 30px;
    line-height: 1.1; letter-spacing: .5px; text-transform: uppercase;
  }
  .contact-list {
    position: absolute; left: 40px; top: 308px; list-style: none;
    color: var(--white); font-size: 15px; line-height: 21px;
  }
  .contact-list li { display: flex; align-items: center; gap: 9px; }
  .contact-list svg { width: 12px; height: 12px; flex: none; }
  .address {
    position: absolute; right: 30px; top: 238px; text-align: right;
    color: var(--white); font-size: 15px; line-height: 21px; font-style: normal;
  }
</style>
</head>
<body>
<main class="canvas">
  <section class="card card--back" aria-label="Card back">
    <div class="back-field" role="img" aria-label="Blue background with a faint repeating brand pattern"></div>
    <span class="back-name">Velran</span>
  </section>

  <section class="card card--front" aria-label="Card front">
    <svg class="front-shapes" viewBox="0 0 700 400" width="700" height="400" aria-hidden="true">
      <path d="M0,400 L0,298 C260,290 520,230 700,112 L700,400 Z" fill="var(--blue-bright)"/>
      <path d="M110,289 C320,281 530,221 700,97" fill="none" stroke="var(--green)" stroke-width="7"/>
    </svg>

    <h1 class="brand-name">Velran<br>Global Components</h1>

    <ul class="contact-list">
      <li><svg viewBox="0 0 12 12"><path d="M2 1l2 0 1 3-1.5 1a6 6 0 003 3L7.5 7l3 1v2c-5 1-10-4-8.5-9z" fill="var(--green)"/></svg>555 014-2731</li>
      <li><svg viewBox="0 0 12 12"><rect x="3" y="0.5" width="6" height="11" rx="1" fill="none" stroke="var(--green)" stroke-width="1.2"/></svg>555 014-2796</li>
      <li><svg viewBox="0 0 12 12"><rect x="0.5" y="2.5" width="11" height="7" fill="var(--green)"/><path d="M0.5 2.5L6 7l5.5-4.5" fill="none" stroke="var(--blue-bright)" stroke-width="1"/></svg>hello@velrancomponents-example.co.uk</li>
      <li><svg viewBox="0 0 12 12"><circle cx="6" cy="6" r="5.3" fill="var(--green)"/><path d="M0.7 6h10.6M6 0.7c-3 3-3 7.6 0 10.6M6 0.7c3 3 3 7.6 0 10.6" fill="none" stroke="var(--blue-bright)" stroke-width=".8"/></svg>www.velrancomponents-example.co.uk</li>
    </ul>

    <address class="address">17 Marlow Yard, Upper Heath<br>Warwick, CV31 8QL, UK</address>
  </section>
</main>
</body>
</html>
```